4D Cradle Glimpse Luxury Ultrasound Billboard

Design a HIGH-END, MODERN billboard for my private prenatal ultrasound studio, 4D Cradle Glimpse, located in Pace, Florida.
This billboard will be viewed by drivers traveling at highway speeds, so it must be extremely clean, simple, and readable within 6 seconds.
About My Business
4D Cradle Glimpse is a private prenatal ultrasound studio specializing in:
Highest technology 4D/HD Ultrasounds
Early Gender Determination
Pregnancy Confirmation
I have been serving families for nearly 10 years and is known for creating a memorable experience, not just an ultrasound appointment.
Design Style
I DO NOT want:
Flowers
Leaves
Swirls
Glitter
Hearts everywhere
Busy backgrounds
Generic maternity stock graphics
I DO want:
Modern
Luxury
Upscale
Clean
Professional
Eye-catching
Premium medical spa feel
Colors
Use colors from my logo:
LOGO Green ( or a deep green)
Black
White
Soft Gold accents
Images:
Incorporate my professional headshot in a clean, modern way, logo, and the ultrasound images
Text
Keep wording minimal.
Primary Headline ( OPEN TO IDEAS) :
EXAMPLES ( WOULD RATHER SOMETHING MORE CATCHY)
" ADVANCED IMAGING. UNFORGETTABLE MOMENTS"
"MEET YOUR BABY BEFORE BIRTH"
Under headline:
4D Ultrasound • Early Gender • Pregnancy Confirmation
Business Name:
4D Cradle Glimpse
Private Prenatal Ultrasound Studio
Phone Number:
850-471-5923
Important
This billboard must be readable in 5–6 seconds from a moving vehicle.
Less text is better.
The phone number and business name must be visible from a distance.
The design should feel like a premium brand that immediately tells expecting parents:
“This is where I go to see my baby.”
Files Provided
Official logo
Headshot
Ultrasound images
Don’t make this look like a medical office billboard.
Make it look like a luxury baby experience billboard. That’s what separates 4D Cradle Glimpse from hospitals, OB offices, and all the new studios popping up around you. The emotional connection is what gets moms to book. ❤️
Billboard Size - 10.6” x 36”

```html
<!DOCTYPE html>
<html lang="en">
<head>
<meta charset="utf-8">
<title>4D Cradle Glimpse – Billboard</title>
<link rel="stylesheet" href="https://fonts.googleapis.com/css2?family=Josefin+Sans:wght@300;400;600&family=Great+Vibes&display=swap">
<style>
  :root{
    --black:#0a0a0a;
    --panel:#050505;
    --white:#ffffff;
    --gold:#e2b63f;
    --gold-light:#f3d36a;
    --gold-deep:#b88a22;
    --grey:#c9c9c9;
  }
  *{margin:0;padding:0;box-sizing:border-box}
  html,body{width:1200px;height:375px;overflow:hidden;background:var(--black)}
  .billboard{position:relative;width:1200px;height:375px;background:var(--black);overflow:hidden;font-family:"Josefin Sans",sans-serif}
  .left-panel{position:absolute;left:0;top:32px;width:660px;height:343px;
    background:radial-gradient(ellipse at 30% 20%,#161616 0%,var(--panel) 60%)}
  .wave-area{position:absolute;left:0;top:190px;width:660px;height:185px;
    background:linear-gradient(170deg,rgba(0,0,0,0) 10%,rgba(184,138,34,.28) 45%,rgba(60,45,15,.35) 60%,rgba(0,0,0,0) 90%)}
  .brand{position:absolute;left:57px;top:62px;width:275px;text-align:center}
  .brand-name{font-size:36px;font-weight:600;color:var(--gold);line-height:1.05}
  .brand-tag{margin-top:14px;font-size:11.5px;font-weight:600;letter-spacing:.6px;color:var(--grey);text-transform:uppercase}
  .headline{position:absolute;left:370px;top:40px;width:290px;text-align:center;color:var(--white)}
  .headline .lead{font-size:44px;font-weight:300;letter-spacing:1px;line-height:1}
  .headline .main{display:block;margin-top:2px;font-size:112px;font-weight:400;line-height:1;
    background:linear-gradient(180deg,var(--gold-light),var(--gold-deep));-webkit-background-clip:text;background-clip:text;color:transparent}
  .headline .script{display:block;margin-top:-4px;font-family:"Great Vibes",cursive;font-size:62px;line-height:1.1}
  .scan-frame{position:absolute;left:740px;top:25px;width:190px;height:220px;transform:rotate(3deg);
    border:4px solid var(--gold);background:var(--black);padding:6px}
  .scan-image{width:100%;height:100%;background:radial-gradient(ellipse at 50% 45%,#b06a5c 0%,#7a3f35 45%,#1a0d0a 100%)}
  .seal{position:absolute;left:684px;top:154px;width:98px;height:98px;border-radius:50%;
    background:radial-gradient(circle at 40% 35%,var(--gold-light),var(--gold-deep));
    display:flex;flex-direction:column;align-items:center;justify-content:center;color:#1a1408}
  .seal::before{content:"";position:absolute;inset:7px;border-radius:50%;border:1px solid rgba(40,30,10,.55)}
  .seal .word{font-family:"Great Vibes",cursive;font-size:20px;line-height:1}
  .seal .small{font-size:10.5px;font-weight:600;line-height:1.25;text-align:center}
  .portrait-ring{position:absolute;left:955px;top:20px;width:285px;height:285px;border-radius:50%;
    border:2.5px solid var(--gold);border-right-color:transparent;border-bottom-color:transparent;transform:rotate(-20deg)}
  .portrait{position:absolute;left:990px;top:27px;width:190px;height:276px;border-radius:95px 95px 8px 8px;
    background:linear-gradient(180deg,#d9c6a6 0%,#c9a88a 35%,#2f4a35 70%,#1d2e22 100%)}
  .services{position:absolute;left:661px;top:272px;font-size:14px;font-weight:600;color:var(--white);letter-spacing:.4px;white-space:nowrap}
  .rule{position:absolute;left:660px;top:303px;width:540px;height:1px;background:var(--gold-deep)}
  .location{position:absolute;left:417px;top:325px;display:flex;align-items:center;gap:8px;color:var(--gold);font-size:26px;font-weight:400}
  .dash{display:inline-block;width:24px;height:1.5px;background:var(--gold)}
  .divider{position:absolute;left:734px;top:323px;width:1px;height:35px;background:var(--gold-deep)}
  .contact{position:absolute;left:764px;top:325px;display:flex;align-items:center;gap:14px;font-size:26px}
  .contact .cta{color:var(--gold);font-weight:400}
  .contact .phone{color:var(--white);font-weight:600;font-size:27px;letter-spacing:.5px}
</style>
</head>
<body>
<div class="billboard">
  <div class="left-panel"></div>
  <div class="wave-area" role="img" aria-label="Soft flowing gold and black light waves"></div>

  <div class="brand">
    <div class="brand-name">4D Cradle Glimpse</div>
    <div class="brand-tag">Prenatal Ultrasound Studio</div>
  </div>

  <h1 class="headline">
    <span class="lead">MEET YOUR</span>
    <span class="main">BABY</span>
    <span class="script">Before Birth</span>
  </h1>

  <div class="scan-frame"><div class="scan-image" role="img" aria-label="4D ultrasound image of twin babies face to face"></div></div>

  <div class="seal">
    <span class="word">Cherish</span>
    <span class="small">EVERY<br>MOMENT</span>
  </div>

  <div class="portrait-ring"></div>
  <div class="portrait" role="img" aria-label="Professional headshot of the studio owner"></div>

  <div class="services">4D ULTRASOUND · EARLY GENDER · PREGNANCY</div>
  <div class="rule"></div>

  <div class="location">
    <span class="dash"></span>
    <svg width="20" height="26" viewBox="0 0 20 26" aria-hidden="true"><path d="M10 0C4.5 0 0 4.4 0 9.8 0 17 10 26 10 26s10-9 10-16.2C20 4.4 15.5 0 10 0zm0 14a4 4 0 110-8 4 4 0 010 8z" fill="var(--gold)"/></svg>
    <span>PACE, FLORIDA</span>
    <span class="dash"></span>
  </div>

  <div class="divider"></div>

  <div class="contact">
    <span class="cta">CALL NOW</span>
    <span class="dash"></span>
    <span class="phone">850-471-5923</span>
    <svg width="26" height="26" viewBox="0 0 24 24" aria-hidden="true"><path d="M6.6 10.8a15.1 15.1 0 006.6 6.6l2.2-2.2a1 1 0 011-.25 11.4 11.4 0 003.6.57 1 1 0 011 1V20a1 1 0 01-1 1A17 17 0 013 4a1 1 0 011-1h3.5a1 1 0 011 1c0 1.25.2 2.45.57 3.57a1 1 0 01-.25 1z" fill="var(--gold)"/><path d="M14 2.5a7.5 7.5 0 017.5 7.5M14 6a4 4 0 014 4" stroke="var(--gold)" stroke-width="1.6" fill="none" stroke-linecap="round"/></svg>
  </div>
</div>
</body>
</html>
```